Webdesign for a business that converts shops into apps. UPDATE BRIEF

We want a creative/professional design for our new business Vorbo.

Vorbo is a service that can deliver instant apps for quillora shops. So every shop owner can have its own app for selling to there customers.

We are open for your interpretation of the design. We think it could be intersting doing an onepage design for this. But thats not set in stones offcourse.

We need several section:
top section
some facts abt the service and maybe our company
price table
some customer review
functionalitys of the app (in a nice way shown)
Section showing screens of a demo shop.
footer with ccdetails, socialmedia, newsletter

I have been playing abit myself with a theme, but no development/designer experience. And we really need a very professional and custom look.

Ps. we are an ecommerce company so if we find any good designer here, we will have enough work for you.

Some competitors in this field;

http://shrt.example/k7Tq2Zw
http://shrt.example/p3Nx9Ld

Here is a design we like
http://brelunoweb.example/

Hoping for some great concepts!

Kind Regards and good luck!

Some screenshots which can be used for app demo;

UPDATE BRIEF

We would like to add a section for features of the app.
We would like to show a zelphone screen and all the most important features of the app and when clicking every feature the screen would change or the feature intened would be high lighted in some way.

The features and any content and info abt that can be used from
https://www.tovexa.example/features.html/

We need an how it works section aswell in the design, also that can be used content from here
https://www.tovexa.example/how-it-works/

Tovexa is our partner, so there work way and features are same as ours. We just want it in a different 'look and feel/design)

Reason: Getting very few good design at the moment. Same designers seem to be responding whith 5 designs at a time of low quality.

Target Market(s)

quillora webshop

Industry/Entity Type

Business

Number of Pages Required

1 page

Font styles to use
Sans Serif

Colors
0355a3
3176b5
85acd3
85cae6
33a6d7
0392cd
f59195
33b8a4

Requirements
Must have
• a creative and custom look, not a copied theme vibe.
Nice to have
• it would be nice if the entire design has a nice flow goinf through the site. The customers experience should be on point.
Should not have
• boring static experience

```html
<!DOCTYPE html>
<html lang="en">
<head>
<meta charset="utf-8">
<title>Vorbo – quillora shop apps</title>
<link rel="stylesheet" href="https://fonts.googleapis.com/css2?family=Open+Sans:wght@300;400;600;700&family=Comfortaa:wght@700&display=swap">
<style>
:root{
  --blue:#0355a3;
  --blue-mid:#3176b5;
  --blue-light:#85acd3;
  --sky:#33a6d7;
  --teal:#33b8a4;
  --red:#e2383f;
  --ink:#333a40;
  --muted:#9a9fa4;
  --line:#e4e6e8;
  --soft:#f4f5f6;
  --white:#ffffff;
}
*{margin:0;padding:0;box-sizing:border-box}
html,body{width:1200px;height:3579px;overflow:hidden}
body{position:relative;font-family:"Open Sans",Arial,sans-serif;color:var(--ink);background:var(--white)}
.abs{position:absolute}
.display{font-family:"Comfortaa","Open Sans",sans-serif;font-weight:700;letter-spacing:1px;text-align:center;position:absolute;left:0;width:1200px}

/* header */
.header{top:0;left:0;width:1200px;height:119px;background:var(--white)}
.logo{left:131px;top:28px;font-family:"Open Sans",Arial,sans-serif;font-size:54px;font-weight:600;color:var(--blue);letter-spacing:-1px}
.nav a{position:absolute;top:62px;font-size:14px;color:#444;text-decoration:none}
.nav a.active{color:#e84c3d}
.nav .home-icon{position:absolute;left:500px;top:40px}

/* hero */
.hero{top:119px;left:0;width:1200px;height:494px;background:linear-gradient(90deg,#6d7c86 0%,#3e4a52 40%,#232a30 100%)}
.hero-title{left:723px;top:390px;font-size:32px;line-height:43px;color:var(--white);font-weight:300}
.hero-title b{font-weight:700}
.btn{position:absolute;display:block;text-align:center;color:var(--white);font-size:13px;line-height:36px;height:36px}
.btn-dark{background:#2b3035}
.btn-blue{background:var(--blue)}

/* welcome */
.welcome-title{top:670px;font-size:44px;color:var(--teal)}
.welcome-lead{left:140px;top:728px;width:920px;text-align:center;font-size:14px;line-height:23px;color:#555}
.feature{position:absolute;top:810px;width:260px;text-align:center}
.feature svg{display:block;margin:0 auto}
.feature h3{font-size:21px;font-weight:400;color:var(--blue-mid);margin-top:18px}
.feature p{font-size:11px;line-height:15px;color:var(--muted);margin-top:8px;padding:0 26px}

/* pricing */
.pricing{top:1033px;left:0;width:1200px;height:482px;background:var(--teal)}
.pricing-title{top:1090px;font-size:44px;color:var(--white)}
.plan{position:absolute;top:1166px;width:306px;height:306px;border-radius:50%;background:var(--white);text-align:center;overflow:hidden}
.plan h3{margin-top:42px;font-size:25px;line-height:32px;font-weight:600;color:var(--blue)}
.plan .price{font-size:24px;line-height:30px;font-weight:700;color:var(--red)}
.plan .price small{font-size:13px;font-weight:400}
.plan ul{list-style:none;margin-top:10px;font-size:10.5px;color:#555}
.plan li{padding:5px 0;border-bottom:1px solid #eee;width:200px;margin:0 auto;line-height:14px}
.plan li:last-child{border:0}
.plan .signup{display:inline-block;margin-top:10px;background:var(--teal);color:var(--white);font-size:13px;padding:0 20px;line-height:34px;height:34px}

/* reviews */
.reviews{top:1515px;left:0;width:1200px;height:453px;background:var(--soft)}
.reviews-title{top:1570px;font-size:44px;color:var(--blue-mid)}
.review{position:absolute;top:1653px;width:298px}
.review .card{background:var(--white);height:148px;padding:22px 26px;box-shadow:0 1px 4px rgba(0,0,0,.12);position:relative}
.review .card p{font-size:11px;line-height:18px;color:var(--muted);text-indent:28px}
.review .quote{position:absolute;left:20px;top:14px;font-size:40px;line-height:40px;color:#ccc;font-family:Georgia,serif}
.review .tail{position:absolute;right:34px;bottom:-14px}
.author{position:absolute;top:174px;right:20px;display:flex;align-items:center;gap:8px}
.author .name{font-size:14px;color:#444}
.author .name small{font-size:10px;color:var(--muted)}
.author .stars{font-size:9px;color:#f5a623;letter-spacing:1px;text-align:right}
.author .avatar{width:36px;height:36px;background:linear-gradient(#c9b8a6,#8e7a68);border:2px solid #ddd}
.dots{top:1897px;left:560px;display:flex;gap:12px}
.dots i{width:8px;height:8px;border-radius:50%;background:#c5c8cb;display:block}
.dots i.on{background:var(--sky)}

/* functionality */
.func-title{top:2032px;font-size:44px;color:var(--teal)}
.func{position:absolute;display:flex;gap:12px;width:320px}
.func svg{flex:none;margin-top:2px}
.func h4{font-size:20px;font-weight:400;color:#3a3f44;line-height:24px}
.func p{font-size:10.5px;color:var(--muted);line-height:14px}

/* demo */
.demo-bg{top:2427px;left:0;width:1200px;height:286px;background:linear-gradient(90deg,#4d4a4a,#6e6a68 45%,#8a8583)}
.demo-base{top:2713px;left:0;width:1200px;height:401px;background:#eceeef}
.demo-title{top:2513px;font-size:40px;color:var(--white)}
.play{top:2571px;left:575px}
.screen{position:absolute;top:2684px;width:222px;height:377px;background:var(--white);box-shadow:0 1px 5px rgba(0,0,0,.25);overflow:hidden}
.screen .bar{height:18px;background:#222}
.screen .fill{height:359px;background:linear-gradient(#f7f7f7,#e3e3e3)}

/* newsletter */
.news-title{top:3155px;font-size:40px;color:var(--teal)}
.field{position:absolute;top:3212px;height:38px;border:1px solid #ccc;background:var(--white);font-size:12px;color:#999;padding:0 14px;line-height:36px}
.subscribe{position:absolute;top:3212px;left:790px;width:98px;height:38px;background:var(--teal);color:var(--white);font-size:12px;font-weight:600;text-align:center;line-height:38px}

/* footer */
.footer{top:3293px;left:0;width:1200px;height:286px;background:var(--soft);border-top:1px solid var(--line)}
.fcol{position:absolute;top:3330px}
.fcol h5{font-size:15px;font-weight:600;color:#333;margin-bottom:12px}
.fcol p,.fcol li{font-size:10.5px;line-height:17px;color:#777;list-style:none}
.fdiv{position:absolute;top:3328px;width:1px;height:150px;background:#dcdcdc}
.links{display:flex;gap:50px}
.social{display:flex;gap:8px}
.social i{width:26px;height:26px;border-radius:50%;background:#666;display:block}
.copy{left:131px;top:3530px;font-size:11px;color:#555}
.copy-line{left:131px;top:3510px;width:938px;height:1px;background:#dcdcdc}
.totop{left:1040px;top:3522px}
</style>
</head>
<body>

<!-- header -->
<header class="abs header">
  <div class="abs logo">Vorbo</div>
  <nav class="nav">
    <svg class="home-icon" width="16" height="14" viewBox="0 0 16 14"><path d="M8 1 1 7h2v6h4V9h2v4h4V7h2z" fill="#e84c3d"/></svg>
    <a class="active" style="left:492px" href="#">Home</a>
    <a style="left:556px" href="#">About</a>
    <a style="left:622px" href="#">Services</a>
    <a style="left:699px" href="#">Pricing</a>
    <a style="left:768px" href="#">Reviews</a>
    <a style="left:843px" href="#">App</a>
    <a style="left:894px" href="#">Screens &amp; Demo</a>
    <a style="left:1018px" href="#">Support</a>
  </nav>
</header>

<!-- hero -->
<section class="abs hero" role="img" aria-label="Photo of a hand holding a smartphone showing a shop app, blurred store interior behind"></section>
<svg class="abs" style="left:22px;top:350px" width="16" height="30" viewBox="0 0 16 30"><path d="M14 2 2 15l12 13" stroke="#fff" stroke-opacity=".6" stroke-width="3" fill="none"/></svg>
<svg class="abs" style="left:1160px;top:350px" width="16" height="30" viewBox="0 0 16 30"><path d="M2 2l12 13L2 28" stroke="#fff" stroke-opacity=".6" stroke-width="3" fill="none"/></svg>
<h1 class="abs hero-title"><b>Direct</b> meer omzet met<br>een quillora app</h1>
<a class="btn btn-dark" style="left:854px;top:485px;width:100px">Learn More</a>
<a class="btn btn-blue" style="left:971px;top:485px;width:93px">Get App</a>

<!-- welcome -->
<h2 class="display welcome-title">Welcome</h2>
<p class="abs welcome-lead">Maecenas consectetur risus sed commodo consectetur. Fusce eleifend nisi vitae elit malesuada, eu pretium turpis tristique. Integer non mollis dui. Suspendisse volutpat dui et lectus pulvinar, eu cursus libero tempor.</p>

<div class="feature" style="left:107px">
  <svg width="56" height="56" viewBox="0 0 56 56" fill="none" stroke="#0355a3" stroke-width="2.5"><path d="M8 48 30 26M14 4l8 8-4 4-8-8M36 20l12-12M38 6a10 10 0 0 0 12 12L36 32 24 20zM30 34l14 14 4-4-14-14"/></svg>
  <h3>Easy setup</h3><p>Donec odio nulla, ultricies eget consequat id, blandit eu dui. Morbi accumsan lorem quis maximus mattis.</p>
</div>
<div class="feature" style="left:348px">
  <svg width="56" height="56" viewBox="0 0 56 56" fill="none" stroke="#0355a3" stroke-width="2.5"><rect x="16" y="3" width="24" height="50" rx="3"/><path d="M16 10h24M16 44h24"/><circle cx="28" cy="48.5" r="1.5"/></svg>
  <h3>On-the-go</h3><p>Donec odio nulla, ultricies eget consequat id, blandit eu dui. Morbi accumsan lorem quis maximus mattis.</p>
</div>
<div class="feature" style="left:590px">
  <svg width="56" height="56" viewBox="0 0 56 56" fill="none" stroke="#0355a3" stroke-width="2.5"><circle cx="28" cy="28" r="24"/><ellipse cx="28" cy="28" rx="11" ry="24"/><path d="M4 28h48M8 16h40M8 40h40"/></svg>
  <h3>Social connect</h3><p>Donec odio nulla, ultricies eget consequat id, blandit eu dui. Morbi accumsan lorem quis maximus mattis.</p>
</div>
<div class="feature" style="left:832px">
  <svg width="56" height="56" viewBox="0 0 56 56" fill="none" stroke="#0355a3" stroke-width="2.5"><circle cx="28" cy="28" r="24"/><circle cx="28" cy="28" r="10"/><path d="M21 21 11 11M35 21l10-10M21 35 11 45M35 35l10 10"/></svg>
  <h3>Dedicated support</h3><p>Donec odio nulla, ultricies eget consequat id, blandit eu dui. Morbi accumsan lorem quis maximus mattis.</p>
</div>

<!-- pricing -->
<section class="abs pricing"></section>
<h2 class="display pricing-title">Pricing</h2>
<div class="plan" style="left:134px">
  <h3>Package#1</h3><div class="price">$00.00<small>/month</small></div>
  <ul><li>Phasellus a velit commodo sagittis.</li><li>Aenean non vulputate erat, nec luctus est.</li><li>Aliquam fringilla quam eget</li><li>Curabitur eros felis</li></ul>
  <a class="signup">Sign Up Now</a>
</div>
<div class="plan" style="left:447px">
  <h3>Package#2</h3><div class="price">$00.00<small>/month</small></div>
  <ul><li>Phasellus a velit commodo sagittis.</li><li>Aenean non vulputate erat, nec luctus est.</li><li>Aliquam fringilla quam eget</li><li>Curabitur eros felis</li></ul>
  <a class="signup">Sign Up Now</a>
</div>
<div class="plan" style="left:760px">
  <h3>Package#3</h3><div class="price">$00.00<small>/month</small></div>
  <ul><li>Phasellus a velit commodo sagittis.</li><li>Aenean non vulputate erat, nec luctus est.</li><li>Aliquam fringilla quam eget</li><li>Curabitur eros felis</li></ul>
  <a class="signup">Sign Up Now</a>
</div>

<!-- reviews -->
<section class="abs reviews"></section>
<h2 class="display reviews-title">Some customer reviews</h2>
<div class="review" style="left:136px">
  <div class="card"><span class="quote">&ldquo;</span><p>Mauris quis sodales enim, semper ultricies massa. Pellentesque risus dolor, tristique vel facilisis at, laoreet ut elit. Fusce id augue at metus cursus pulvinar. In nec lectus porttitor, porttitor velit vel, tempus tortor.</p>
  <svg class="tail" width="26" height="14" viewBox="0 0 26 14"><path d="M0 0h26L4 14z" fill="#fff"/></svg></div>
  <div class="author"><div><div class="name">Tom Reval, <small>City name</small></div><div class="stars">★★★★★</div></div><div class="avatar" role="img" aria-label="Customer portrait"></div></div>
</div>
<div class="review" style="left:451px">
  <div class="card"><span class="quote">&ldquo;</span><p>Mauris quis sodales enim, semper ultricies massa. Pellentesque risus dolor, tristique vel facilisis at, laoreet ut elit. Fusce id augue at metus cursus pulvinar. In nec lectus porttitor, porttitor velit vel, tempus tortor.</p>
  <svg class="tail" width="26" height="14" viewBox="0 0 26 14"><path d="M0 0h26L4 14z" fill="#fff"/></svg></div>
  <div class="author"><div><div class="name">Tom Reval, <small>City name</small></div><div class="stars">★★★★★</div></div><div class="avatar" role="img" aria-label="Customer portrait"></div></div>
</div>
<div class="review" style="left:768px">
  <div class="card"><span class="quote">&ldquo;</span><p>Mauris quis sodales enim, semper ultricies massa. Pellentesque risus dolor, tristique vel facilisis at, laoreet ut elit. Fusce id augue at metus cursus pulvinar. In nec lectus porttitor, porttitor velit vel, tempus tortor.</p>
  <svg class="tail" width="26" height="14" viewBox="0 0 26 14"><path d="M0 0h26L4 14z" fill="#fff"/></svg></div>
  <div class="author"><div><div class="name">Tom Reval, <small>City name</small></div><div class="stars">★★★★★</div></div><div class="avatar" role="img" aria-label="Customer portrait"></div></div>
</div>
<div class="abs dots"><i class="on"></i><i></i><i></i><i></i></div>

<!-- functionality -->
<h2 class="display func-title">Functionalitys of the App</h2>
<div class="func" style="left:131px;top:2118px"><svg width="36" height="30" viewBox="0 0 36 30" fill="#6b7075"><circle cx="12" cy="16" r="9"/><circle cx="12" cy="16" r="3.5" fill="#fff"/><circle cx="27" cy="8" r="6"/><circle cx="27" cy="8" r="2.2" fill="#fff"/><circle cx="27" cy="23" r="4"/></svg><div><h4>User Settings</h4><p>Donec odio nulla, ultricies eget consequat id</p></div></div>
<div class="func" style="left:460px;top:2118px"><svg width="36" height="30" viewBox="0 0 36 30" fill="#6b7075"><path d="M2 5h32v22H2z"/><path d="M2 5l16 12L34 5" stroke="#fff" stroke-width="2" fill="none"/></svg><div><h4>Messages Inbox</h4><p>Donec odio nulla, ultricies eget consequat id</p></div></div>
<div class="func" style="left:787px;top:2118px"><svg width="36" height="30" viewBox="0 0 36 30" fill="#6b7075"><circle cx="18" cy="8" r="6"/><path d="M7 28c0-8 5-12 11-12s11 4 11 12z"/><circle cx="6" cy="11" r="4"/><circle cx="30" cy="11" r="4"/><path d="M0 26c0-6 3-9 6-9s4 1 4 1-3 4-3 8zM36 26c0-6-3-9-6-9s-4 1-4 1 3 4 3 8z"/></svg><div><h4>Friends List</h4><p>Donec odio nulla, ultricies eget consequat id</p></div></div>

<div class="func" style="left:131px;top:2206px"><svg width="36" height="30" viewBox="0 0 36 30" fill="#6b7075"><path d="M2 3h20v13H9l-5 4v-4H2z"/><path d="M14 19h11l5 4v-4h4V8h-9v11z" opacity=".75"/></svg><div><h4>Live Chat Messages</h4><p>Donec odio nulla, ultricies eget consequat id</p></div></div>
<div class="func" style="left:460px;top:2206px"><svg width="36" height="30" viewBox="0 0 36 30" fill="none" stroke="#6b7075" stroke-width="2.5"><rect x="5" y="5" width="26" height="23"/><path d="M5 11h26M11 2v6M25 2v6M10 16h4M16 16h4M22 16h4M10 22h4M16 22h4M22 22h4"/></svg><div><h4>Calendar / Planner</h4><p>Donec odio nulla, ultricies eget consequat id</p></div></div>
<div class="func" style="left:787px;top:2206px"><svg width="36" height="30" viewBox="0 0 36 30" fill="#6b7075"><path d="M18 2a9 9 0 0 0-9 9c0 7 9 17 9 17s9-10 9-17a9 9 0 0 0-9-9z"/><circle cx="18" cy="11" r="3.5" fill="#fff"/></svg><div><h4>My Places</h4><p>Donec odio nulla, ultricies eget consequat id</p></div></div>

<div class="func" style="left:131px;top:2301px"><svg width="36" height="30" viewBox="0 0 36 30" fill="#6b7075"><circle cx="16" cy="15" r="13"/><path d="M12 8v14l11-7z" fill="#fff"/></svg><div><h4>Media Player™</h4><p>Donec odio nulla, ultricies eget consequat id</p></div></div>
<div class="func" style="left:460px;top:2301px"><svg width="36" height="30" viewBox="0 0 36 30" fill="none" stroke="#6b7075" stroke-width="3"><circle cx="16" cy="15" r="11"/><path d="M16 15V8M16 15l5 4"/></svg><div><h4>Intuitive Statistics</h4><p>Donec odio nulla, ultricies eget consequat id</p></div></div>
<div class="func" style="left:787px;top:2301px"><svg width="36" height="30" viewBox="0 0 36 30" fill="#6b7075"><path d="M9 26a7 7 0 0 1 0-14 9 9 0 0 1 17-2 7 7 0 0 1 2 16z"/></svg><div><h4>Weather on-the-go</h4><p>Donec odio nulla, ultricies eget consequat id</p></div></div>

<!-- demo -->
<section class="abs demo-bg" role="img" aria-label="Photo of a hand browsing a shop catalogue with watches on a table"></section>
<section class="abs demo-base"></section>
<h2 class="display demo-title">DEMO</h2>
<svg class="abs play" width="50" height="50" viewBox="0 0 50 50"><circle cx="25" cy="25" r="24" fill="#fff"/><path d="M19 14v22l18-11z" fill="#3a3a3a"/></svg>
<div class="screen" style="left:131px"><div class="bar"></div><div class="fill" role="img" aria-label="Demo shop app screen: product list"></div></div>
<div class="screen" style="left:370px"><div class="bar"></div><div class="fill" role="img" aria-label="Demo shop app screen: product grid"></div></div>
<div class="screen" style="left:608px"><div class="bar"></div><div class="fill" role="img" aria-label="Demo shop app screen: product detail"></div></div>
<div class="screen" style="left:847px"><div class="bar"></div><div class="fill" role="img" aria-label="Demo shop app screen: checkout"></div></div>

<!-- newsletter -->
<h2 class="display news-title">Newsletter</h2>
<div class="field" style="left:313px;width:221px">Name</div>
<div class="field" style="left:554px;width:219px">Email</div>
<div class="subscribe">SUBSCRIBE</div>

<!-- footer -->
<footer class="abs footer"></footer>
<div class="fcol" style="left:131px;width:230px"><h5>About Us</h5><p>Fusce posuere urna vel erat posuere gravida. Sed interdum erat dolor, quis vulputate arcu dignissim in. Donec lobortis, sapien eget imperdiet porta, quam ligula blandit tellus, eu fermentum felis nisi ac massa. Sed massa dolor, pharetra nec dignissim eu, hendrerit eget ipsum. Duis molestie feugiat felis non.</p></div>
<div class="fdiv" style="left:383px"></div>
<div class="fcol" style="left:413px"><h5>Links</h5><div class="links"><ul><li>› Home</li><li>› About</li><li>› Services</li><li>› Pricing</li><li>› Reviews</li></ul><ul><li>› App Screens &amp; Demo</li><li>› Support</li><li>› Privacy Policy</li><li>› Terms and conditions</li><li>› Sitemap</li></ul></div></div>
<div class="fdiv" style="left:680px"></div>
<div class="fcol" style="left:704px"><h5>Contact Us</h5><ul><li>• 12, Kade lane, Harborfield</li><li>• Phone : +1 555 010 2040</li><li>• Email : support@vorbo.example</li></ul></div>
<div class="fdiv" style="left:945px"></div>
<div class="fcol" style="left:973px"><h5>Social Media</h5><div class="social"><i></i><i></i><i></i></div></div>
<div class="abs copy-line"></div>
<div class="abs copy">Copyright © 2016 Company name. All rights reserved.</div>
<svg class="abs totop" width="30" height="30" viewBox="0 0 30 30"><circle cx="15" cy="15" r="14" fill="#bfc3c6"/><path d="M9 18l6-6 6 6" stroke="#fff" stroke-width="2.5" fill="none"/></svg>

</body>
</html>
```